Tech business card design

We need an amazing business card design for our new business 'Pexla' a marketing tech startup based in Sydney, Australia. We provide an online marketplace for businesses to search and buy advertising media, connect with service providers and learn more about marketing. We wish to communicate 'cool tech', reliability and professionalism and design based around our logo.

Target Market(s)

Business Owners

Contact Information for Business Card

Name
Position
Email Address
Website
Phone Number

Font styles to use
Other font styles liked:
• Avenir & Avenir Next

Colors

Designer to choose colors to be used in the design.

```html
<!DOCTYPE html>
<html lang="en">
<head>
<meta charset="utf-8">
<title>Pexla Business Card</title>
<link rel="stylesheet" href="https://fonts.googleapis.com/css2?family=Source+Sans+3:wght@400;700;800&display=swap">
<style>
  :root {
    --backdrop: #a0cde0;
    --card: #ffffff;
    --navy: #10123a;
    --rule: #1f2a5c;
    --ink: #2b2d3a;
    --card-edge: #c4c4c4;
  }
  * { margin: 0; padding: 0; box-sizing: border-box; }
  html, body { width: 1200px; height: 1184px; overflow: hidden; }
  body {
    background: var(--backdrop);
    font-family: "Source Sans 3", "Myriad Pro", sans-serif;
    position: relative;
  }
  .card {
    position: absolute;
    left: 149px;
    width: 901px;
    height: 515px;
    background: var(--card);
    border-radius: 34px;
  }
  .card--front { top: 50px; }
  .card--back { top: 596px; border: 2px solid var(--card-edge); }

  .holder { position: absolute; left: 72px; top: 100px; line-height: 1; }
  .holder__name { font-size: 29px; font-weight: 700; color: var(--rule); letter-spacing: 0.2px; }
  .holder__role { font-size: 26px; font-weight: 400; color: var(--ink); margin-top: 2px; }

  .divider { position: absolute; left: 0; right: 0; top: 185px; height: 3px; background: var(--rule); }

  .wordmark {
    position: absolute;
    font-weight: 800;
    color: var(--navy);
    line-height: 1;
    letter-spacing: -1px;
  }
  .card--front .wordmark { left: 70px; top: 326px; font-size: 108px; }

  .contacts { position: absolute; left: 585px; top: 292px; font-size: 22px; color: var(--ink); list-style: none; }
  .contacts li { display: flex; align-items: center; gap: 10px; height: 32px; }
  .contacts svg { width: 22px; height: 22px; flex: none; }
  .contacts .web { letter-spacing: 2px; }
  .contacts .address { display: block; height: auto; line-height: 25px; margin-top: 4px; }

  .frame {
    position: absolute;
    left: 32px; top: 21px;
    width: 833px; height: 469px;
    border: 3px solid var(--navy);
    border-radius: 22px;
  }
  .card--back .wordmark { left: 0; right: 0; top: 128px; text-align: center; font-size: 156px; }
  .back-site {
    position: absolute; left: 0; right: 0; top: 389px;
    text-align: center; font-size: 28px; letter-spacing: 3.5px; color: var(--navy);
  }
</style>
</head>
<body>
  <section class="card card--front">
    <div class="holder">
      <p class="holder__name">JOHN SMITH</p>
      <p class="holder__role">Position</p>
    </div>
    <div class="divider"></div>
    <p class="wordmark">pexla</p>
    <ul class="contacts">
      <li>
        <svg viewBox="0 0 22 22" aria-hidden="true"><circle cx="11" cy="11" r="9.5" fill="none" stroke="#2b2d3a" stroke-width="1.6"/><path d="M13.5 5.5c-2.5 1-4.5 5-3.5 10.5l2-.5c-.6-3.4.3-6.5 2.3-8z" fill="#2b2d3a"/></svg>
        <span>012-345-6789</span>
      </li>
      <li>
        <svg viewBox="0 0 22 22" aria-hidden="true"><rect x="1" y="5" width="20" height="13" fill="#2b2d3a"/><path d="M1 5l10 7 10-7M1 18l7-6M21 18l-7-6" stroke="#fff" stroke-width="1.5" fill="none"/></svg>
        <span>info@pexla.com</span>
      </li>
      <li>
        <svg viewBox="0 0 22 22" aria-hidden="true" fill="none" stroke="#2b2d3a" stroke-width="1.5"><circle cx="11" cy="11" r="9.5"/><ellipse cx="11" cy="11" rx="4" ry="9.5"/><path d="M1.5 11h19M3 6h16M3 16h16M11 1.5v19"/></svg>
        <span class="web">www.pexla.com</span>
      </li>
      <li class="address">Street name City Name,<br>Zipcode,012345</li>
    </ul>
  </section>

  <section class="card card--back">
    <div class="frame"></div>
    <p class="wordmark">pexla</p>
    <p class="back-site">www.pexla.com</p>
  </section>
</body>
</html>
```